Business cards for Harbourline Supply Pty Ltd that import building products into Australia from China
Target Market(s)
Business to Business
Industry/Entity Type
Business
Contact Information for Business Card
Front: Logo and Business Name
Rear:
Desmond Varrick
General Manager
Mobile: 0427 561 394
email: dessie@harbourlinesupply.com.au
alternative email: dessie@outbackworks.com.au
web: www.harbourlinesupply.com.au
Adelaide, Brisbane and Darwin
Colors
ec1f27
fbee3d

```html
<!DOCTYPE html>
<html lang="en">
<head>
<meta charset="utf-8">
<title>Harbourline Supply Pty Ltd — Business Cards</title>
<link href="https://fonts.googleapis.com/css2?family=Open+Sans:wght@400;600;700&family=Saira:wght@600&display=swap" rel="stylesheet">
<style>
  :root {
    --brand-red: #ec1f27;
    --brand-yellow: #fbee3d;
    --ink: #1f1f1f;
    --text: #222222;
    --card-white: #ffffff;
    --backdrop: #b6b6b6;
    --rule: #d9b8bb;
  }
  * { margin: 0; padding: 0; box-sizing: border-box; }
  html, body {
    width: 1200px; height: 900px; overflow: hidden;
    background: var(--backdrop);
    font-family: "Open Sans", Arial, sans-serif;
  }
  .canvas { position: relative; width: 1200px; height: 900px; }
  .card {
    position: absolute; top: 184px; height: 491px;
    border-radius: 14px;
    box-shadow: 3px 4px 6px rgba(0,0,0,0.35);
  }
  .card--details { left: 299px; width: 301px; background: var(--card-white); }
  .card--brand { left: 645px; width: 305px; background: var(--brand-yellow); }

  .brand-lockup {
    position: absolute; left: 0; right: 0;
    display: flex; flex-direction: column; align-items: center; gap: 14px;
  }
  .card--details .brand-lockup { top: 36px; }
  .card--brand .brand-lockup { top: 172px; }
  .brand-square { width: 60px; height: 60px; background: var(--brand-red); }
  .brand-name {
    font-weight: 700; font-size: 23px; line-height: 1.15;
    color: var(--ink); text-align: center; width: 250px;
  }

  .contact-name {
    position: absolute; left: 32px; top: 257px;
    font-family: "Saira", "Open Sans", sans-serif; font-weight: 600;
    font-size: 20px; letter-spacing: 0.3px; color: var(--ink);
  }
  .contact-name .first { color: var(--brand-red); }
  .contact-role {
    position: absolute; left: 33px; top: 281px;
    font-size: 13px; font-weight: 600; color: var(--text);
  }
  .contact-list {
    position: absolute; left: 32px; top: 312px; list-style: none;
  }
  .contact-list li {
    display: flex; align-items: center; gap: 9px;
    height: 22px; font-size: 13.5px; color: var(--text);
  }
  .contact-list svg { width: 12px; height: 12px; flex: none; fill: var(--brand-red); }
  .divider {
    position: absolute; left: 32px; width: 236px; top: 410px;
    border-top: 1px solid var(--rule);
  }
  .locations {
    position: absolute; left: 32px; width: 236px; top: 424px;
    text-align: center; font-size: 13.5px; color: var(--text);
  }
</style>
</head>
<body>
<main class="canvas">
  <section class="card card--details">
    <div class="brand-lockup">
      <div class="brand-square"></div>
      <div class="brand-name">Harbourline Supply Pty Ltd</div>
    </div>

    <h1 class="contact-name"><span class="first">DESMOND</span> VARRICK</h1>
    <p class="contact-role">General Manager</p>
    <ul class="contact-list">
      <li><svg viewBox="0 0 12 12"><path d="M1 4c0-2 2-3 5-3s5 1 5 3l-2 1-1-1H4L3 5zM3 6h6l2 5H1z"/></svg>0427 561 394</li>
      <li><svg viewBox="0 0 12 12"><path d="M1 2h10v8H1zM2 3.2v.4l4 3 4-3v-.4L6 6z" fill-rule="evenodd"/></svg>dessie@harbourlinesupply.com.au</li>
      <li><svg viewBox="0 0 12 12"><path d="M1 2h10v8H1zM2 3.2v.4l4 3 4-3v-.4L6 6z" fill-rule="evenodd"/></svg>dessie@outbackworks.com.au</li>
      <li><svg viewBox="0 0 12 12"><circle cx="6" cy="6" r="5.5"/><path d="M4 2.5l2 2-1 2 2 1v2.5l2-2-1-2-2-1 1-2z" fill="#fff"/></svg>www.harbourlinesupply.com.au</li>
    </ul>
    <div class="divider"></div>
    <p class="locations">Adelaide, Brisbane and Darwin</p>
  </section>

  <section class="card card--brand">
    <div class="brand-lockup">
      <div class="brand-square"></div>
      <div class="brand-name">Harbourline Supply Pty Ltd</div>
    </div>
  </section>
</main>
</body>
</html>
```